Harborline Auto LLC

Car Dealer Customer Service
Address: 2874 Cresthaven Road, Shelbyville, TN 37162
web: www.harborlineautoxq.net
email: harborlineautoxq@mailnest.example
Phone: (931) 555-0148
Phone: (629) 555-0173

```html
<!DOCTYPE html>
<html lang="en">
<head>
<meta charset="utf-8">
<title>Harborline Auto — Business Card</title>
<link href="https://fonts.googleapis.com/css2?family=Poppins:wght@400;600&display=swap" rel="stylesheet">
<style>
  :root {
    --page-bg: #d9d4cc;
    --card-bg: #eceef0;
    --brand-blue: #1f6f9a;
    --brand-blue-deep: #175a80;
    --accent-orange: #e39a2b;
    --name-blue: #1c5a78;
    --text-dark: #1e2326;
    --logo-text: #f3ece6;
  }
  * { margin: 0; padding: 0; box-sizing: border-box; }
  html, body { width: 1200px; height: 1054px; overflow: hidden; }
  body {
    background: var(--page-bg);
    font-family: "Poppins", sans-serif;
    position: relative;
  }
  .business-card {
    position: absolute;
    left: 100px;
    top: 224px;
    width: 1000px;
    height: 605px;
    border-radius: 26px;
    background: var(--card-bg);
    overflow: hidden;
    box-shadow: 0 18px 40px rgba(0,0,0,0.18);
  }
  .card-panel { position: absolute; inset: 0; }
  .brand-block {
    position: absolute;
    left: 0;
    width: 490px;
    top: 0;
    height: 605px;
  }
  .brand-mark-circle {
    position: absolute;
    left: 175px;
    top: 165px;
    width: 140px;
    height: 140px;
    border-radius: 50%;
    background: rgba(255,255,255,0.18);
  }
  .brand-name {
    position: absolute;
    left: 0;
    width: 490px;
    top: 405px;
    text-align: center;
    font-weight: 600;
    font-size: 33px;
    letter-spacing: 0.5px;
    color: var(--logo-text);
  }
  .person {
    position: absolute;
    right: 40px;
    top: 78px;
    text-align: right;
  }
  .person-name {
    font-weight: 600;
    font-size: 35px;
    color: var(--name-blue);
    line-height: 1.2;
  }
  .person-title {
    font-size: 25px;
    color: var(--text-dark);
    line-height: 1.4;
  }
  .address {
    position: absolute;
    right: 40px;
    top: 334px;
    text-align: right;
    font-size: 24px;
    line-height: 1.38;
    color: var(--text-dark);
  }
  .contact-list {
    position: absolute;
    right: 36px;
    top: 418px;
    list-style: none;
  }
  .contact-item {
    display: flex;
    justify-content: flex-end;
    align-items: center;
    gap: 14px;
    height: 35px;
    font-size: 24px;
    color: var(--text-dark);
  }
  .contact-item.phone {
    font-weight: 600;
    color: var(--name-blue);
    letter-spacing: 1px;
  }
  .contact-icon { width: 22px; height: 22px; flex: none; }
</style>
</head>
<body>
  <div class="business-card">
    <svg class="card-panel" width="1000" height="605" viewBox="0 0 1000 605" aria-hidden="true">
      <path d="M0 0 H410 Q530 300 400 605 H0 Z" fill="var(--accent-orange)"/>
      <path d="M0 0 H396 Q510 300 388 605 H0 Z" fill="var(--brand-blue)"/>
    </svg>

    <div class="brand-block">
      <div class="brand-mark-circle"></div>
      <div class="brand-name">HARBORLINE AUTO</div>
    </div>

    <div class="person">
      <div class="person-name">Daniel Corven</div>
      <div class="person-title">Managing Director</div>
    </div>

    <div class="address">
      2874 Cresthaven Road,<br>
      Shelbyville, TN 37162
    </div>

    <ul class="contact-list">
      <li class="contact-item phone">931-555-0148
        <svg class="contact-icon" viewBox="0 0 24 24"><path d="M3 9 Q12 3 21 9 L19 12 L16 10 V8 H8 V10 L5 12 Z M6 13 H18 L19 20 H5 Z" fill="var(--accent-orange)"/></svg>
      </li>
      <li class="contact-item phone">629-555-0173
        <svg class="contact-icon" viewBox="0 0 24 24"><path d="M3 9 Q12 3 21 9 L19 12 L16 10 V8 H8 V10 L5 12 Z M6 13 H18 L19 20 H5 Z" fill="var(--accent-orange)"/></svg>
      </li>
      <li class="contact-item">www.harborlineautoxq.net
        <svg class="contact-icon" viewBox="0 0 24 24"><rect x="2" y="5" width="20" height="14" rx="1.5" fill="var(--accent-orange)"/><path d="M3 6 L12 13 L21 6" stroke="#fff" stroke-width="1.6" fill="none"/></svg>
      </li>
      <li class="contact-item">harborlineautoxq@mailnest.example
        <svg class="contact-icon" viewBox="0 0 24 24"><circle cx="12" cy="12" r="10" fill="var(--accent-orange)"/><path d="M2 12 H22 M12 2 V22 M12 2 Q6 12 12 22 M12 2 Q18 12 12 22" stroke="#fff" stroke-width="1.2" fill="none"/></svg>
      </li>
    </ul>
  </div>
</body>
</html>
```